Very new and innovative Web design for Property managers of Vacation rentals

We are looking for a new website design for travel agencies and property managers specialised on vacation rentals business, holiday villas and apartments.

The end users of this website are travellers who are looking for a vacation home for their next holiday: this is the reason why the website must be easy to use, attractive, professional, possibly elegant and focused on get new reservations.

This is a draft of our current website: https://intro3.kelumsito.com/
Please consider that we would like to have proposals with a totally different and innovative layout, surprise us!

These are the pages of the website:
• Homepage: feel free to redesign all the homepage as you wish, surprise us with something very new! Please consider that Property manager/Travel agencies usually want to have the opportunity to put in evidence groups of houses with specific characteristics (eg. villas with private swimming pool, apartment in big/small towns, villas with air co, etc…), destinations and tourist areas, and sometimes experiences or activities (please consider that the website layout must be suitable even if some of the previous sections are not used).
• Search page: we’d like to organise the results of the search page in three different ways:
o Grid
o Map
o List
• Property page: to illustrate the characteristics, descriptions, images, …. of the property. It is very important to put in evidence images of the property and to maintain the booking form (and the other call to action bottom – eg. whatsapp) always visible
• Custom pages: static pages composed usually by text, images and call to actions
• Contact us (general form)
• Info request (specific of a property form)
• Booking process
• Blog, organised in four pages:
o Home Page – introduction to the blog
o List of articles
o Single article
o Site Map (presentation of categories and sub-categories)

If possible, we’d prefer to receive the material in Adobe XD or similar so that we can obtain the three versions:
- smartphone
- tablet
- desktop

The website will be then developed in Bootstrap: as a result we’ll need the icons in SVG format (or the library used)

In attachment you can find the map of the website pages

```html
<!DOCTYPE html>
<html lang="en">
<head>
<meta charset="utf-8">
<title>Agriturismo Il Poggio – StayNest</title>
<link href="https://fonts.googleapis.com/css2?family=Poppins:wght@300;400;500;600&family=PT+Sans+Narrow:wght@400;700&display=swap" rel="stylesheet">
<style>
:root{
  --green:#0bb07f;
  --green-dark:#07966b;
  --ink:#111;
  --text:#444;
  --muted:#666;
  --line:#e2e2e2;
  --footer:#1c1c1c;
  --white:#fff;
}
*{box-sizing:border-box;margin:0;padding:0}
html,body{width:1200px;height:2206px;overflow:hidden}
body{position:relative;font-family:"Poppins",sans-serif;color:var(--text);background:var(--white)}
.abs{position:absolute}
.heading{font-family:"PT Sans Narrow",sans-serif;color:var(--ink);font-weight:400}

/* hero */
.hero{left:0;top:0;width:1200px;height:244px;background:linear-gradient(180deg,#2a3036 0%,#3d4a52 45%,#3d6f80 75%,#6a8c95 100%)}
.brand{font-family:"Poppins",sans-serif;font-weight:500;font-size:24px;letter-spacing:1.5px;color:var(--white);display:flex;align-items:center;gap:8px}
.brand .dot{width:22px;height:22px;border-radius:50%;background:var(--green)}
.top-links{top:16px;right:108px;display:flex;gap:18px;align-items:center;font-size:11px;color:var(--white)}
.lang{background:var(--green);padding:9px 12px;font-size:10px;font-weight:500}
.main-nav{top:70px;left:537px;display:flex;gap:56px;font-size:14px;font-weight:500;letter-spacing:1px;color:var(--white)}
.hero-title{top:146px;left:0;width:1200px;text-align:center;font-family:"PT Sans Narrow",sans-serif;font-weight:700;font-size:42px;color:var(--white)}
.gallery-btn{left:94px;top:197px;width:118px;height:34px;border-radius:17px;background:#eee;font-family:"PT Sans Narrow",sans-serif;font-size:16px;color:#222;display:flex;align-items:center;justify-content:center}
.fav{left:1060px;top:191px;width:46px;height:46px;border-radius:50%;background:rgba(255,255,255,.35);display:flex;align-items:center;justify-content:center}

.crumbs{left:93px;top:274px;font-size:11px;color:var(--muted);letter-spacing:.3px}
.crumbs span{margin:0 6px}
.crumbs b{font-weight:400;color:#222}

.title{left:93px;top:322px;font-family:"PT Sans Narrow",sans-serif;font-weight:700;font-size:42px;color:var(--ink)}
.type{left:93px;top:384px;font-size:13px;font-style:italic;color:#111}
.stats{left:93px;top:403px;font-size:13px;color:var(--muted);font-weight:300}

.section-h{font-size:26px}
.desc{left:93px;top:498px;width:660px;font-size:13.2px;line-height:21.8px;color:var(--text);font-weight:300}

.share{left:628px;top:642px;width:120px;height:30px;background:#f4f4f4;display:flex;align-items:center;justify-content:space-around;padding:0 6px}
.share i{display:block;width:12px;height:12px;border-radius:50%;background:var(--green)}

.amenities{left:93px;top:690px;width:680px;display:grid;grid-template-columns:266px 266px 148px}
.amenity{display:flex;align-items:center;gap:8px;height:37.5px;width:142px;font-size:13.5px;color:#333;border-bottom:1px solid var(--line)}
.amenity.last{border-bottom:none}
.ic{width:18px;height:18px;flex:none}

/* booking */
.book-shadow{left:796px;top:342px;width:319px;height:343px;background:var(--green)}
.book{left:788px;top:332px;width:319px;height:345px;background:repeating-linear-gradient(45deg,#f7f7f7 0 2px,#fbfbfb 2px 4px);box-shadow:0 0 6px rgba(0,0,0,.06)}
.field{position:absolute;left:28px;width:262px;height:37px;border:1.5px solid #333;background:var(--white);font-size:11.5px;color:#333;display:flex;align-items:center;justify-content:space-between;padding:0 10px 0 12px}
.field.half{width:127px}
.btn{position:absolute;left:28px;width:262px;height:38px;color:var(--white);font-size:12.5px;display:flex;align-items:center;justify-content:center;gap:6px}
.btn.primary{background:var(--green)}
.btn.dark{background:#3a3a3a}

/* gallery / accommodations */
.gallery-img{left:94px;top:920px;width:270px;height:166px;background:linear-gradient(180deg,#8aa6b8 0%,#c9c6bd 45%,#5a5044 62%,#1ea6c9 80%,#3cc2e0 100%)}
.acc{width:133px}
.acc-name{font-size:15.5px;color:var(--green);text-decoration:underline;text-underline-offset:3px}
.acc-row{display:flex;align-items:center;gap:8px;height:33px;border-bottom:1px solid var(--line);font-size:12.5px;color:#333}
.acc-row:last-of-type{border-bottom:none}
.acc-row .lbl{width:70px}
.view-btn{display:inline-block;margin-top:4px;background:var(--green);color:var(--white);font-size:11.5px;padding:9px 10px;margin-left:2px}

.map{left:94px;top:1183px;width:1012px;height:359px;background:linear-gradient(90deg,#a6cf9a 0%,#8ab4f0 28%,#a4cd9a 45%,#8ab4f0 62%,#a9d19e 90%)}

/* footer */
.footer{left:0;top:1591px;width:1200px;height:615px;background:var(--footer);color:var(--white)}
.footer .brand{position:absolute;left:94px;top:92px}
.sub{position:absolute;left:95px;top:160px;width:209px;padding-bottom:8px;border-bottom:2px solid var(--white);font-size:12.5px;letter-spacing:.8px}
.sub-arrow{position:absolute;left:325px;top:180px}
.about{position:absolute;left:95px;top:210px;width:310px;font-size:12.5px;line-height:18px;letter-spacing:.8px;color:#e6e6e6}
.f-h{position:absolute;top:72px;font-size:15px;font-weight:500;letter-spacing:1.5px;color:var(--green)}
.f-nav{position:absolute;left:518px;top:112px;list-style:none;font-size:12.5px;letter-spacing:1.2px;line-height:34.7px;color:#eee}
.post{position:absolute;left:791px;display:flex;gap:11px}
.post-img{width:70px;height:61px}
.post-t{font-size:12px;font-weight:600;color:var(--green);line-height:15px;width:228px}
.post-d{font-size:12px;color:#ddd;margin-top:14px}
.contact{position:absolute;top:362px;display:flex;gap:10px;align-items:center}
.contact b{display:block;color:var(--green);font-size:14.5px;font-weight:600;letter-spacing:1.2px}
.contact span{display:block;font-size:14.5px;letter-spacing:1.2px;line-height:18px}
.vsep{position:absolute;top:338px;width:1px;height:118px;background:#3a3a3a}
.hsep{position:absolute;left:94px;top:458px;width:1012px;height:1px;background:#3a3a3a}
.legal{position:absolute;left:0;width:1200px;text-align:center;font-size:12px;letter-spacing:1.2px;font-weight:500}
.legal .g{color:var(--green)}
.like{position:absolute;top:537px;left:578px;display:flex;gap:6px;align-items:center}
</style>
</head>
<body>

<header>
  <div class="abs hero" role="img" aria-label="Evening photo of a modern villa with pool and wooden deck"></div>
  <div class="abs brand" style="left:94px;top:38px"><i class="dot"></i>StayNest</div>
  <div class="abs top-links">
    <span>Login</span>
    <span>&#9829; Wish List (0)</span>
    <span class="lang">Language &#9662;</span>
  </div>
  <nav class="abs main-nav">
    <span>Last Minute</span><span>Special Offers</span><span>Experience</span><span>Contact Us</span>
  </nav>
  <h1 class="abs hero-title">PROPERTY</h1>
  <div class="abs gallery-btn">Photo Gallery</div>
  <div class="abs fav">
    <svg width="24" height="22" viewBox="0 0 24 22"><path d="M12 20 3 11a5 5 0 0 1 9-6 5 5 0 0 1 9 6z" fill="none" stroke="#fff" stroke-width="2"/></svg>
  </div>
</header>

<div class="abs crumbs">Home Page<span>/</span>Italy<span>/</span>Tuscany<span>/</span>Toscana<span>/</span>Casa Santa Lidia<span>/</span><b>Agriturismo Il Poggio</b></div>

<h2 class="abs title">Agriturismo Il Poggio</h2>
<div class="abs type">Country House / Farm House</div>
<div class="abs stats">Accommodations: 2 Sleeps: 7 Bedrooms: 2 Bathrooms: 2</div>

<h3 class="abs heading section-h" style="left:92px;top:458px">Description</h3>
<p class="abs desc">il casale è immerso nella campagna toscana ma a soli 3 km dal paese più vicino dove potete trovare tutti i negozi con le principali comodità.<br>La piscina ad uso condiviso con i due appartamenti è di dimensioni 5*3 e profonda 1,30 mt , è recintata e aperta tutti i giorni dalle ore 09:00 alle ore 20:00.<br>è possibile affittare entrambi gli appartamenti per avere l'esclusività e la totale indipendenza.</p>

<h3 class="abs heading section-h" style="left:92px;top:638px">Amenities</h3>
<div class="abs share">
  <svg width="14" height="11" viewBox="0 0 14 11"><rect x="0.5" y="0.5" width="13" height="10" fill="none" stroke="#0bb07f"/><path d="M1 1l6 5 6-5" fill="none" stroke="#0bb07f"/></svg>
  <i></i><i></i><i></i><i></i>
</div>

<div class="abs amenities">
  <div class="amenity"><svg class="ic" viewBox="0 0 18 18"><circle cx="9" cy="7" r="6" fill="#0bb07f"/><rect x="8" y="12" width="2" height="6" fill="#0bb07f"/></svg>Garden</div>
  <div class="amenity"><svg class="ic" viewBox="0 0 18 18"><path d="M2 9 9 3l7 6v7H2z" fill="#0bb07f"/></svg>Near Village</div>
  <div class="amenity"><svg class="ic" viewBox="0 0 18 18"><g stroke="#0bb07f" stroke-width="2"><path d="M9 1v16M1 9h16M3 3l12 12M15 3 3 15"/></g></svg>Internet</div>
  <div class="amenity"><svg class="ic" viewBox="0 0 18 18"><rect x="1" y="7" width="16" height="7" fill="#0bb07f"/><rect x="1" y="3" width="2" height="13" fill="#0bb07f"/><rect x="15" y="3" width="2" height="13" fill="#0bb07f"/></svg>Baby Bed</div>
  <div class="amenity"><svg class="ic" viewBox="0 0 18 18"><circle cx="9" cy="4" r="3" fill="#0bb07f"/><path d="M3 17c0-6 12-6 12 0z" fill="#0bb07f"/></svg>Maid</div>
  <div class="amenity"><svg class="ic" viewBox="0 0 18 18"><rect x="1" y="1" width="16" height="16" rx="3" fill="#0bb07f"/><path d="M7 13V5h3a2.5 2.5 0 0 1 0 5H7" fill="none" stroke="#fff" stroke-width="2"/></svg>Parking</div>
  <div class="amenity"><svg class="ic" viewBox="0 0 18 18"><path d="M4 2v12M14 2v12M4 6h10M4 10h10" stroke="#0bb07f" stroke-width="2"/><path d="M1 16q4-3 8 0t8 0" fill="none" stroke="#0bb07f" stroke-width="2"/></svg>Swimmingpool</div>
  <div class="amenity"><svg class="ic" viewBox="0 0 18 18"><path d="M9 16 2 9a4 4 0 0 1 7-5 4 4 0 0 1 7 5z" fill="#0bb07f"/></svg>Weedding</div>
  <div class="amenity"><svg class="ic" viewBox="0 0 18 18"><circle cx="9" cy="9" r="8" fill="#0bb07f"/><circle cx="9" cy="9" r="4" fill="#fff"/></svg>Breakfast</div>
  <div class="amenity last"><svg class="ic" viewBox="0 0 18 18"><g fill="none" stroke="#0bb07f" stroke-width="2"><path d="M1 7a11 11 0 0 1 16 0M4 10a7 7 0 0 1 10 0M6.5 13a3 3 0 0 1 5 0"/></g></svg>Internet Wifi</div>
</div>

<aside>
  <div class="abs book-shadow"></div>
  <form class="abs book">
    <div class="field" style="top:26px">Accommodation <span>&#8962; &#711;</span></div>
    <div class="field" style="top:79px">Check In <span>&#9638; &#711;</span></div>
    <div class="field" style="top:132px">Check Out <span>&#9638; &#711;</span></div>
    <div class="field half" style="top:183px">Travelers <span>&#9679; &#711;</span></div>
    <div class="field half" style="top:183px;left:164px">Pets <span>&#9679; &#711;</span></div>
    <div class="btn primary" style="top:238px">&#9889; Book Now</div>
    <div class="btn dark" style="top:279px">&#9993; Info Request</div>
  </form>
</aside>

<h3 class="abs heading section-h" style="left:92px;top:875px">Gallery</h3>
<div class="abs gallery-img" role="img" aria-label="Photo of a modern white villa with pool at dusk"></div>

<h3 class="abs heading section-h" style="left:527px;top:875px">Accommodations</h3>
<div class="abs acc" style="left:528px;top:930px">
  <div class="acc-name">Casa Livia</div>
  <div style="margin-top:12px">
    <div class="acc-row"><svg class="ic" viewBox="0 0 18 18"><rect x="2" y="2" width="14" height="14" fill="#0bb07f"/></svg><span class="lbl">Sleeps</span>4</div>
    <div class="acc-row"><svg class="ic" viewBox="0 0 18 18"><rect x="1" y="8" width="16" height="6" fill="#0bb07f"/><rect x="1" y="4" width="6" height="4" fill="#0bb07f"/></svg><span class="lbl">Bed Room</span>1</div>
    <div class="acc-row"><svg class="ic" viewBox="0 0 18 18"><path d="M1 9h16v3a4 4 0 0 1-4 4H5a4 4 0 0 1-4-4z" fill="#0bb07f"/><rect x="9" y="2" width="3" height="7" fill="#0bb07f"/></svg><span class="lbl">Bathroom</span>1</div>
  </div>
  <span class="view-btn">View Details</span>
</div>
<div class="abs acc" style="left:744px;top:930px">
  <div class="acc-name">Casa Marta</div>
  <div style="margin-top:12px">
    <div class="acc-row"><svg class="ic" viewBox="0 0 18 18"><rect x="2" y="2" width="14" height="14" fill="#0bb07f"/></svg><span class="lbl">Sleeps</span>3</div>
    <div class="acc-row"><svg class="ic" viewBox="0 0 18 18"><rect x="1" y="8" width="16" height="6" fill="#0bb07f"/><rect x="1" y="4" width="6" height="4" fill="#0bb07f"/></svg><span class="lbl">Bed Room</span>1</div>
    <div class="acc-row"><svg class="ic" viewBox="0 0 18 18"><path d="M1 9h16v3a4 4 0 0 1-4 4H5a4 4 0 0 1-4-4z" fill="#0bb07f"/><rect x="9" y="2" width="3" height="7" fill="#0bb07f"/></svg><span class="lbl">Bathroom</span>1</div>
  </div>
  <span class="view-btn">View Details</span>
</div>

<div class="abs map" role="img" aria-label="Map of central Italy and the Adriatic showing the property location"></div>

<footer class="abs footer">
  <div class="brand"><i class="dot"></i>StayNest</div>
  <div class="sub">Subscribe to our Newsletter</div>
  <svg class="sub-arrow" width="40" height="12" viewBox="0 0 40 12"><path d="M0 6h38M32 1l6 5-6 5" fill="none" stroke="#0bb07f" stroke-width="1.5"/></svg>
  <p class="about">Our range of services is very large, and we are constantly expanding it.</p>

  <div class="f-h" style="left:516px">Navigation</div>
  <ul class="f-nav"><li>Last Minute</li><li>Special Offers</li><li>Experience</li><li>Contact Us</li></ul>

  <div class="f-h" style="left:791px">Recent posts</div>
  <div class="post" style="top:115px">
    <div class="post-img" role="img" aria-label="Photo of sun loungers by a pool" style="background:linear-gradient(180deg,#6d7a5a,#c2a06a 55%,#4fa7d6)"></div>
    <div><div class="post-t">Which construction tool is better to choose?</div><div class="post-d">2 November, 2020</div></div>
  </div>
  <div class="post" style="top:200px">
    <div class="post-img" role="img" aria-label="Photo of a rustic room with a table tennis table" style="background:linear-gradient(180deg,#7a4a2c,#d8d2c6 55%,#5a86a8)"></div>
    <div><div class="post-t">Which construction tool is better to choose?</div><div class="post-d">2 November, 2020</div></div>
  </div>

  <div class="contact" style="left:122px">
    <svg width="30" height="30" viewBox="0 0 30 30"><path d="M6 2l6 6-3 4q3 6 9 9l4-3 6 6-4 4Q12 28 2 6z" fill="#0bb07f"/></svg>
    <div><b>Call us</b><span>+1 555 010 4477 (USA)</span></div>
  </div>
  <div class="vsep" style="left:434px"></div>
  <div class="contact" style="left:485px">
    <svg width="40" height="30" viewBox="0 0 40 30"><rect x="1.5" y="1.5" width="37" height="27" rx="3" fill="none" stroke="#0bb07f" stroke-width="2.5"/><path d="M3 4l17 13L37 4" fill="none" stroke="#0bb07f" stroke-width="2.5"/></svg>
    <div><b>Write to us</b><span>hello@staynest.example</span></div>
  </div>
  <div class="vsep" style="left:763px"></div>
  <div class="contact" style="left:824px">
    <svg width="30" height="42" viewBox="0 0 30 42"><path d="M15 40S2 24 2 15a13 13 0 0 1 26 0c0 9-13 25-13 25z" fill="none" stroke="#0bb07f" stroke-width="2.5"/><circle cx="15" cy="15" r="5" fill="none" stroke="#0bb07f" stroke-width="2.5"/></svg>
    <div><b>Office location</b><span>12-40 Harbor Ln, Maplewood, NY 10000</span></div>
  </div>
  <div class="hsep"></div>

  <div class="legal" style="top:483px">Privacy Policies &nbsp;&nbsp;/&nbsp;&nbsp; Reservation Policies &nbsp;&nbsp;/&nbsp;&nbsp; Cookie Policy</div>
  <div class="legal" style="top:501px">Copyright © 2021 StayNest. All Rights Reserved. <span class="g">Powered by StayNest</span></div>
  <div class="like">
    <svg width="16" height="16" viewBox="0 0 16 16"><circle cx="8" cy="8" r="8" fill="#fff"/></svg>
    <svg width="56" height="15" viewBox="0 0 56 15"><rect width="56" height="15" rx="2" fill="#4267b2"/></svg>
  </div>
</footer>

</body>
</html>
```